Calden L - Premium Business Cards

Background of Calden L
Calden Leafworks is a cigar mobile lounge where guests become family. A place of luxury, relaxation, and ambiance is the global popularity demand. Calden Leafworks strives to provide first-class service of quality and products. Our goal is to ensure that every guest is treated and serviced as a VIP.

Calden Leafworks was founded by Dennis Markow Jr in January 2020. After 15 years of cigar reviews and research Dennis decided it was time to launch his own cigar brand and boutique cigar company. With a wealth of knowledge and years of experience Calden Leafworks was born. With opulence for all cultures, Calden Leafworks offers hand rolled cigars with premium blend tobacco from sweet to bold imported from Costa Rica, Dominican Republic, and Nicaragua. Thank you for your business!

Objective:
Create a business card template to be used for all employees. Design should communicate premium and classy. And should use earth tone colors.

Design should include:
1. Client wants to incorporate the cigar leaf
2. Logo
3. Tagline: Savor Every Draw
3. Content info:
Kevin Oldacre
Owner
555-017-4863
koldacre@caldenleaf.com
caldenleafworks.com

```html
<!DOCTYPE html>
<html lang="en">
<head>
<meta charset="UTF-8">
<title>Calden Leafworks — Business Cards</title>
<link rel="stylesheet" href="https://fonts.googleapis.com/css2?family=Montserrat:wght@600;700&family=Open+Sans:wght@400;600&display=swap">
<style>
  :root {
    --stage: #1e1e1e;
    --card-dark: #231f20;
    --card-light: #ffffff;
    --ink: #231f20;
    --ink-soft: #3a3a3a;
    --rule: #8a8a8a;
    --on-dark: #ffffff;
  }
  * { margin: 0; padding: 0; box-sizing: border-box; }
  html, body {
    width: 1200px; height: 1015px; overflow: hidden;
    background: var(--stage);
  }
  .stage { position: relative; width: 1200px; height: 1015px; }
  .card {
    position: absolute; left: 250px; width: 700px; height: 400px;
    box-shadow: 0 14px 30px rgba(0,0,0,.6);
    overflow: hidden;
  }
  .card--front { top: 70px; background: var(--card-dark); color: var(--on-dark); }
  .card--back  { top: 545px; background: var(--card-light); color: var(--ink); }

  .brand {
    position: absolute;
    display: flex; flex-direction: column; align-items: center; gap: 14px;
  }
  .wordmark {
    font-family: "Montserrat", sans-serif;
    font-weight: 700;
    letter-spacing: 2px;
    text-transform: uppercase;
    line-height: 1.1;
    white-space: nowrap;
    display: flex; align-items: center; gap: 12px;
  }
  .wordmark__dot {
    width: 10px; height: 10px; border-radius: 50%;
    background: currentColor; flex: none;
  }
  .brand__rule {
    display: flex; align-items: center; width: 62%;
  }
  .brand__rule::before, .brand__rule::after {
    content: ""; width: 5px; height: 5px; border-radius: 50%;
    background: currentColor; flex: none;
  }
  .brand__rule span { flex: 1; height: 1px; background: currentColor; opacity: .8; }

  .card--front .brand { top: 140px; left: 0; right: 0; }
  .card--front .wordmark { font-size: 40px; }
  .card--front .site {
    position: absolute; top: 300px; left: 0; right: 0; text-align: center;
    font-family: "Open Sans", sans-serif; font-size: 18px; letter-spacing: 1.5px;
  }

  .card--back .brand { top: 128px; left: 30px; width: 320px; color: var(--ink); }
  .card--back .wordmark { font-size: 22px; letter-spacing: 1.5px; }

  .divider {
    position: absolute; left: 370px; top: 70px; width: 1px; height: 180px;
    background: var(--rule);
  }
  .contact {
    position: absolute; left: 400px; top: 72px;
    font-family: "Open Sans", sans-serif;
  }
  .contact__name {
    font-family: "Montserrat", sans-serif; font-weight: 700;
    font-size: 22px; letter-spacing: .5px; text-transform: uppercase;
  }
  .contact__role { font-size: 16px; color: var(--ink-soft); margin-bottom: 14px; }
  .contact__line {
    display: flex; align-items: center; gap: 8px;
    font-size: 16px; line-height: 26px; color: var(--ink);
  }
  .contact__line svg { width: 15px; height: 15px; flex: none; }
  .tagline-band {
    position: absolute; left: 0; right: 0; bottom: 0; height: 80px;
    background: var(--card-dark); color: var(--on-dark);
    display: flex; align-items: center; justify-content: center;
    font-family: "Montserrat", sans-serif; font-weight: 600;
    font-size: 22px; letter-spacing: 3px; text-transform: uppercase;
  }
</style>
</head>
<body>
<main class="stage">
  <section class="card card--front" aria-label="Card front">
    <div class="brand">
      <div class="wordmark"><span class="wordmark__dot"></span>Calden Leafworks</div>
      <div class="brand__rule"><span></span></div>
    </div>
    <p class="site">www.caldenleafworks.com</p>
  </section>

  <section class="card card--back" aria-label="Card back">
    <div class="brand">
      <div class="wordmark"><span class="wordmark__dot"></span>Calden Leafworks</div>
      <div class="brand__rule"><span></span></div>
    </div>
    <div class="divider"></div>
    <div class="contact">
      <p class="contact__name">Kevin Oldacre</p>
      <p class="contact__role">Owner</p>
      <p class="contact__line">
        <svg viewBox="0 0 16 16" aria-hidden="true"><path d="M4 1.5l2.5 3-1.5 1.5c.8 1.8 2.2 3.2 4 4l1.5-1.5 3 2.5-1.5 2.5C7 13.5 2.5 9 1.5 3z" fill="var(--ink)"/></svg>
        555-017-4863
      </p>
      <p class="contact__line">
        <svg viewBox="0 0 16 16" aria-hidden="true"><rect x="1" y="3" width="14" height="10" fill="var(--ink)"/><path d="M1 3l7 6 7-6" stroke="#fff" stroke-width="1.2" fill="none"/></svg>
        koldacre@caldenleaf.com
      </p>
      <p class="contact__line">
        <svg viewBox="0 0 16 16" aria-hidden="true"><circle cx="8" cy="8" r="6.5" fill="none" stroke="var(--ink)" stroke-width="1.4"/><ellipse cx="8" cy="8" rx="2.8" ry="6.5" fill="none" stroke="var(--ink)" stroke-width="1.2"/><path d="M1.5 8h13" stroke="var(--ink)" stroke-width="1.2"/></svg>
        caldenleafworks.com
      </p>
    </div>
    <div class="tagline-band">Savor Every Draw</div>
  </section>
</main>
</body>
</html>
```